Small corporate website template design

I need a couple templates designed for a small corporate website. The corporate site reflects the existence of the parent company which will own various brands/services that have their own websites, so it will mainly be used to present who we are, what we do, what is happening (news/events), how to contact us, link off to our other brand/service sites, as well as post information for public relations, investors, and job opportunities.

The company name is Brelvanto LLC (www.brelvanto-example.com), and the name is representative of stratified layers of interconnected digital services. The corporate site is not expected to generate a bunch of fanfare - that honor will be reserved for the externally linked brand/service sites.

The provided logo may be manipulated in color, size, shape, positioning, etc. to get it to fit with the design, but should be integrated in some way.

What we are looking for is a home page layout as well as a template for an inner page whereby the navigation/logo, etc may be diminished to some extent for the inner pages. We are also interested in reusable elements such as dividers, content containers, etc. in order to represent the types of information described above that we would like to present as described above.

We are particularly interested in consistency of design elements, conservative use of color (including consideration of accessibility concerns), judicious use of whitespace in favor of simplified messaging, and something lending itself well to internationalization/translation.

Target Market(s)

Small business owners, entrepreneurs (B2B)

Number of Pages Required

2 page

Font styles to use
Sans Serif

Requirements
Must have
• See the attached PDF with the logo concept, color swatches, and comparative sites.

```html
<!DOCTYPE html>
<html lang="en">
<head>
<meta charset="utf-8">
<title>Brelvanto LLC</title>
<link rel="stylesheet" href="https://fonts.googleapis.com/css2?family=Montserrat:wght@400;600;700&family=Open+Sans:wght@400;600;700&display=swap">
<style>
:root{
  --navy-deep:#0d2b57;
  --navy:#1f4a85;
  --navy-band:#2b5893;
  --footer-blue:#5585c4;
  --orange:#f7890b;
  --grey-bg:#e9e9e9;
  --ink:#111;
  --body-ink:#444;
  --white:#fff;
  --purple:#6a3bbf;
}
*{margin:0;padding:0;box-sizing:border-box}
html,body{width:1200px;height:2597px;overflow:hidden}
body{position:relative;font-family:"Open Sans",Arial,sans-serif;background:var(--white);color:var(--ink)}
a{text-decoration:none}
.abs{position:absolute}

/* hero */
.hero{left:0;top:0;width:1200px;height:1247px;background:var(--grey-bg)}
.hero-bg{left:0;top:0;width:1200px;height:600px}
.brand{left:130px;top:24px;text-align:center;width:120px}
.brand-mark{width:56px;height:56px;border-radius:50%;background:var(--white);margin:0 auto 12px}
.brand-name{font-family:"Montserrat",Arial,sans-serif;font-weight:600;font-size:16px;color:var(--white)}
.nav{top:26px;left:554px;display:flex;align-items:center;font-family:"Montserrat",Arial,sans-serif;font-size:13px;color:var(--white)}
.nav a{color:inherit;margin-right:40px;line-height:28px}
.nav .active{background:var(--white);color:var(--navy-deep);padding:0 10px;margin-right:24px}
.search{width:28px;height:28px;border:2px solid var(--white);border-radius:50%;display:flex;align-items:center;justify-content:center}
.hero-title{left:211px;top:200px;font-family:"Montserrat",Arial,sans-serif;font-size:37px;line-height:47px;color:var(--white);font-weight:700}
.hero-title span{font-weight:400;display:block}
.btn{display:inline-block;background:var(--orange);color:var(--ink);font-family:"Montserrat",Arial,sans-serif;font-weight:700;font-size:15px;text-align:center;line-height:43px}
.hero-btn{left:216px;top:378px;width:181px}
.hero-art{left:600px;top:156px;width:430px;height:510px;border-radius:30px;background:radial-gradient(ellipse at 55% 45%,#b690f0 0%,#7b48cf 45%,rgba(106,59,191,0.15) 80%,transparent 100%)}

/* about */
.about-art{left:147px;top:770px;width:407px;height:382px;border-radius:12px;background:linear-gradient(135deg,#f0d44f 0%,#e86a3c 50%,#3fa7c9 100%);opacity:.85}
.tag{left:663px;top:784px;border:1.5px solid var(--ink);padding:0 9px;line-height:27px;font-family:"Montserrat",Arial,sans-serif;font-weight:700;font-size:14px}
.about-title{left:663px;top:845px;font-family:"Montserrat",Arial,sans-serif;font-size:36px;line-height:41px;font-weight:400}
.about-title .accent{color:var(--orange);font-weight:700;display:block}
.about-text{left:663px;top:992px;width:410px;font-size:13px;line-height:18px;color:var(--body-ink)}
.about-btn{left:667px;top:1117px;width:114px;line-height:36px}

/* services */
.section-title{left:0;width:1200px;text-align:center;font-family:"Montserrat",Arial,sans-serif;font-size:26px;font-weight:400}
.pill{left:578px;top:1379px;width:45px;height:7px;border-radius:4px;background:#d0d0d0}
.divider{top:1490px;width:1px;height:252px;background:#d8d8d8}
.service{top:1505px;width:250px}
.service-icon{width:66px;height:66px;border-radius:50%;background:var(--navy);display:flex;align-items:center;justify-content:center}
.service h3{font-family:"Montserrat",Arial,sans-serif;font-size:14px;font-weight:700;margin-top:25px}
.service p{font-size:12px;line-height:15px;color:var(--body-ink);margin-top:13px;width:195px}
.more{display:block;margin-top:18px;font-family:"Montserrat",Arial,sans-serif;font-size:10px;font-weight:700;color:var(--orange);text-decoration:underline}

/* testimonials */
.testimonials{left:0;top:1845px;width:1200px;height:381px;background:var(--navy-band);color:var(--white)}
.testimonials .section-title{top:60px;font-weight:700}
.quote{left:385px;top:155px;width:430px;text-align:center;font-size:13px;line-height:16px}
.qmark{font-family:"Montserrat",Arial,sans-serif;font-weight:700;font-size:54px;line-height:1}
.author{left:0;width:1200px;top:292px;text-align:center;font-family:"Montserrat",Arial,sans-serif;font-size:10px;font-weight:700;color:var(--orange);text-decoration:underline}
.place{left:0;width:1200px;top:312px;text-align:center;font-size:11px}

/* footer */
.footer{left:0;top:2226px;width:1200px;height:371px;background:var(--footer-blue);color:var(--white)}
.footer-brand{left:190px;top:70px;width:100px;text-align:center}
.footer-brand .brand-mark{width:92px;height:92px;margin-bottom:22px}
.footer-brand .brand-name{font-size:16px}
.f-head{font-family:"Montserrat",Arial,sans-serif;font-weight:700;font-size:12px;top:68px}
.f-list{font-size:11px;line-height:17px}
.f-row{display:flex;align-items:flex-start;gap:12px;margin-bottom:17px}
.social{display:flex;align-items:center;gap:12px;margin-bottom:14px;font-size:11px}
.dot{width:26px;height:26px;border-radius:50%;background:var(--navy-deep)}
.f-rule{left:130px;top:282px;width:940px;height:1px;background:rgba(255,255,255,.3)}
.copy{left:0;width:1200px;top:320px;text-align:center;font-size:11px}
</style>
</head>
<body>

<section class="hero abs">
  <svg class="hero-bg abs" width="1200" height="600" viewBox="0 0 1200 600" aria-hidden="true">
    <defs>
      <linearGradient id="heroGrad" x1="0" y1="0" x2="1" y2="1">
        <stop offset="0" stop-color="#0b2853"/>
        <stop offset="1" stop-color="#2a5a9c"/>
      </linearGradient>
    </defs>
    <polygon points="0,0 1200,0 1200,330 0,592" fill="#2b5c9c"/>
    <polygon points="0,0 1200,0 1200,312 0,566" fill="url(#heroGrad)"/>
  </svg>

  <div class="brand abs"><div class="brand-mark"></div><div class="brand-name">Brelvanto</div></div>

  <nav class="nav abs">
    <a class="active" href="#">Home</a>
    <a href="#">Who we are</a>
    <a href="#">What we do</a>
    <a href="#">News</a>
    <a href="#">Contact Us</a>
    <span class="search"><svg width="12" height="12" viewBox="0 0 12 12"><circle cx="5" cy="5" r="3.5" fill="none" stroke="#fff" stroke-width="1.6"/><line x1="7.6" y1="7.6" x2="10.5" y2="10.5" stroke="#fff" stroke-width="1.6"/></svg></span>
  </nav>

  <h1 class="hero-title abs">Adaptive Software<br>Technology for the<span>Digital Revolution</span></h1>
  <a class="btn hero-btn abs" href="#">Job Opportunities</a>
  <div class="hero-art abs" role="img" aria-label="Isometric illustration of a laptop with floating media cards and two people working"></div>

  <div class="about-art abs" role="img" aria-label="Flat line illustration of a computer screen connected to mail, cloud, video and image icons"></div>
  <div class="tag abs">WHO WE ARE</div>
  <h2 class="about-title abs">Digital Advertising<span class="accent">Business Management</span>Services</h2>
  <p class="about-text abs">Sed ut perspiciatis unde omnis iste natus error sit voluptatem accusantium doloremque laudantium, totam rem aperiam, eaque ipsa quae ab illo inventore veritatis et quasi architecto beatae vitae dicta sunt explicabo. Nemo enim ipsam voluptatem quia voluptas sit aspernatur aut odit aut fugit, sed quia</p>
  <a class="btn about-btn abs" href="#">Read More</a>
</section>

<h2 class="section-title abs" style="top:1321px">What we do</h2>
<div class="pill abs"></div>
<div class="divider abs" style="left:404px"></div>
<div class="divider abs" style="left:783px"></div>

<div class="service abs" style="left:132px">
  <div class="service-icon"><svg width="30" height="34" viewBox="0 0 30 34"><path d="M4 2h15l7 7v23H4z" fill="#fff"/><circle cx="20" cy="24" r="5" fill="none" stroke="#1f4a85" stroke-width="2"/><line x1="23.5" y1="27.5" x2="27" y2="31" stroke="#fff" stroke-width="3"/><rect x="8" y="11" width="10" height="2" fill="#1f4a85"/><rect x="8" y="16" width="8" height="2" fill="#1f4a85"/></svg></div>
  <h3>Paid Search</h3>
  <p>Sed ut perspiciatis unde omnis iste natus error sit voluptatem accusan doloremque laudantium, totam rem aperiam, eaque ipsa quae.</p>
  <a class="more" href="#">READ MORE</a>
</div>
<div class="service abs" style="left:500px">
  <div class="service-icon"><svg width="34" height="30" viewBox="0 0 34 30"><rect x="2" y="2" width="30" height="19" fill="#fff"/><rect x="14" y="21" width="6" height="5" fill="#fff"/><rect x="9" y="26" width="16" height="2" fill="#fff"/></svg></div>
  <h3>Agency Display</h3>
  <p>Sed ut perspiciatis unde omnis iste natus error sit voluptatem accusan doloremque laudantium, totam rem aperiam, eaque ipsa quae.</p>
  <a class="more" href="#">READ MORE</a>
</div>
<div class="service abs" style="left:878px">
  <div class="service-icon"><svg width="34" height="34" viewBox="0 0 34 34"><circle cx="13" cy="20" r="9" fill="none" stroke="#fff" stroke-width="5" stroke-dasharray="4 3"/><circle cx="13" cy="20" r="3" fill="#fff"/><circle cx="25" cy="9" r="5" fill="none" stroke="#fff" stroke-width="3" stroke-dasharray="3 2"/></svg></div>
  <h3>Development</h3>
  <p>Sed ut perspiciatis unde omnis iste natus error sit voluptatem accusan doloremque laudantium, totam rem aperiam, eaque ipsa quae.</p>
  <a class="more" href="#">READ MORE</a>
</div>

<section class="testimonials abs">
  <h2 class="section-title abs">Testimonials</h2>
  <svg class="abs" style="left:132px;top:166px" width="16" height="26" viewBox="0 0 16 26"><polyline points="13,2 3,13 13,24" fill="none" stroke="#4b7fc4" stroke-width="2.5"/></svg>
  <svg class="abs" style="left:1052px;top:166px" width="16" height="26" viewBox="0 0 16 26"><polyline points="3,2 13,13 3,24" fill="none" stroke="#4b7fc4" stroke-width="2.5"/></svg>
  <div class="qmark abs" style="left:378px;top:122px">&ldquo;</div>
  <p class="quote abs">Sed ut perspiciatis unde omnis iste natus error sit voluptatem accusantium doloremque laudantium, totam rem aperiam, eaque ipsa quae ab illo inventore veritatis et quasi architecto beatae vitae dicta sunt explicabo. Nemo enim ipsam voluptatem quia voluptas sit aspernatur aut odit aut fugit, sed quia</p>
  <div class="qmark abs" style="left:728px;top:232px">&rdquo;</div>
  <div class="author abs">MARCUS DELAINE</div>
  <div class="place abs">England</div>
</section>

<footer class="footer abs">
  <div class="footer-brand abs"><div class="brand-mark"></div><div class="brand-name">Brelvanto</div></div>

  <div class="f-head abs" style="left:416px">CONTACT US</div>
  <div class="f-list abs" style="left:416px;top:102px">
    <div class="f-row"><svg width="8" height="12" viewBox="0 0 8 12"><path d="M4 0a4 4 0 0 1 4 4c0 3-4 8-4 8S0 7 0 4a4 4 0 0 1 4-4z" fill="#fff"/><circle cx="4" cy="4" r="1.5" fill="#5585c4"/></svg><span>781 Larkfield Road<br>Westmoor, IL 60911</span></div>
    <div class="f-row"><svg width="10" height="10" viewBox="0 0 10 10"><path d="M1 1l3 0 1 2.5-1.5 1a6 6 0 0 0 3 3l1-1.5L10 7v2.5C5 10 0 5 1 1z" fill="#fff"/></svg><span>555.010.0142</span></div>
    <div class="f-row"><svg width="11" height="8" viewBox="0 0 11 8"><rect width="11" height="8" fill="#fff"/><polyline points="0,0 5.5,4.5 11,0" fill="none" stroke="#5585c4" stroke-width="1"/></svg><span>info@brelvanto-example.com</span></div>
  </div>

  <div class="f-head abs" style="left:689px">MENU</div>
  <div class="f-list abs" style="left:689px;top:102px">Home<br>Who we are<br>What we do<br>News<br>Contact Us</div>

  <div class="f-head abs" style="left:937px">CONNECT WITH US</div>
  <div class="abs" style="left:938px;top:104px">
    <div class="social"><span class="dot"></span>Friendbook</div>
    <div class="social"><span class="dot" style="background:#1f8fd6"></span>Chirper</div>
    <div class="social"><span class="dot"></span>Linkwork</div>
  </div>

  <div class="f-rule abs"></div>
  <div class="copy abs">Copyrights @ 2018 All Rights Reserved</div>
</footer>

</body>
</html>
```